Business Card Design Project

Business Card
We are rebranding with a new logo
Industry/Entity Type
Business
Contact Information for Business Card
Dennis Morvale +61 487215963 dennis@quorv.com.au P.O. Box 872 Fernlow QLD 4309
Requirements
Must have
- Logo

```html
<!DOCTYPE html>
<html lang="en">
<head>
<meta charset="utf-8">
<title>Quorv International – Business Card</title>
<link rel="stylesheet" href="https://fonts.googleapis.com/css2?family=PT+Sans:wght@400;700&display=swap">
<style>
  :root {
    --page-bg: #2a2a2a;
    --card-white: #f4f4f4;
    --brand-blue: #0f86b8;
    --blue-light: #1fa3d6;
    --blue-deep: #0b6a94;
    --brand-orange: #e8781f;
    --orange-dark: #d9561a;
    --text-white: #ffffff;
  }
  html, body {
    margin: 0;
    width: 1200px;
    height: 915px;
    overflow: hidden;
    background: var(--page-bg);
    font-family: "PT Sans", Arial, sans-serif;
  }
  .card {
    position: absolute;
    left: 100px;
    top: 172px;
    width: 1000px;
    height: 570px;
    overflow: hidden;
  }
  .card-art {
    position: absolute;
    inset: 0;
    width: 1000px;
    height: 570px;
  }
  .brand-name {
    position: absolute;
    left: 100px;
    top: 210px;
    margin: 0;
    font-size: 54px;
    font-weight: 700;
    color: var(--brand-blue);
    letter-spacing: 0.5px;
  }
  .contact {
    position: absolute;
    right: 58px;
    top: 305px;
    text-align: right;
    color: var(--text-white);
  }
  .contact-name {
    margin: 0 0 22px;
    font-size: 30px;
    font-weight: 700;
    color: var(--brand-orange);
    letter-spacing: 0.3px;
  }
  .contact-address {
    margin: 0 0 14px;
    font-style: normal;
    font-size: 24px;
    line-height: 32px;
    padding-right: 2px;
  }
  .contact-lines {
    list-style: none;
    margin: 0;
    padding: 0;
    font-size: 24px;
    line-height: 32px;
  }
  .contact-lines li {
    display: flex;
    justify-content: flex-end;
    align-items: center;
    gap: 12px;
  }
  .contact-icon {
    width: 22px;
    height: 22px;
    flex: none;
  }
</style>
</head>
<body>
  <main class="card">
    <svg class="card-art" viewBox="0 0 1000 570" aria-hidden="true">
      <defs>
        <radialGradient id="blueGlow" cx="0.72" cy="0.45" r="0.7">
          <stop offset="0" stop-color="var(--blue-light)"/>
          <stop offset="1" stop-color="var(--blue-deep)"/>
        </radialGradient>
      </defs>
      <rect class="panel-blue" width="1000" height="570" fill="url(#blueGlow)"/>
      <path class="swoosh-dark" d="M0,0 L150,0 C560,20 800,170 705,330 C640,430 500,515 410,570 L0,570 Z" fill="var(--orange-dark)"/>
      <path class="swoosh-orange" d="M0,0 L140,0 C545,22 775,170 682,330 C620,432 485,512 395,570 L0,570 Z" fill="var(--brand-orange)"/>
      <path class="panel-white" d="M0,0 L120,0 C520,25 745,170 655,330 C600,430 470,510 380,570 L0,570 Z" fill="var(--card-white)" stroke="#ffffff" stroke-width="3"/>
    </svg>

    <p class="brand-name">Quorv International</p>

    <section class="contact">
      <p class="contact-name">DENNIS MORVALE</p>
      <address class="contact-address">P.O. Box 872<br>Fernlow QLD 4309</address>
      <ul class="contact-lines">
        <li>+61 487215963
          <svg class="contact-icon" viewBox="0 0 22 22" aria-hidden="true">
            <path d="M3,9 C3,5 19,5 19,9 L15,10 L15,8 L7,8 L7,10 Z" fill="var(--brand-orange)"/>
            <path d="M7,11 L15,11 L18,18 L4,18 Z" fill="var(--brand-orange)"/>
          </svg>
        </li>
        <li>dennis@quorv.com.au
          <svg class="contact-icon" viewBox="0 0 22 22" aria-hidden="true">
            <rect x="2" y="6" width="18" height="11" fill="var(--brand-orange)"/>
            <path d="M2,6 L11,13 L20,6" fill="none" stroke="var(--blue-deep)" stroke-width="1.5"/>
          </svg>
        </li>
        <li>www.quorv.com.au
          <svg class="contact-icon" viewBox="0 0 22 22" aria-hidden="true">
            <circle cx="11" cy="11" r="8" fill="var(--brand-orange)"/>
            <path d="M3,11 H19 M11,3 C7,7 7,15 11,19 M11,3 C15,7 15,15 11,19" fill="none" stroke="var(--blue-deep)" stroke-width="1.2"/>
          </svg>
        </li>
      </ul>
    </section>
  </main>
</body>
</html>
```